Poster for a new "Pizza Roll" Combo at our bakery

We are a cinnamon roll and coffee focused bakery, but we would like an innovative poster design to bring attention to our new offering, a Pizza Roll. We will be offering it as a combo, and this is what we wish to advertise. It will be geared mainly towards a younger high school aged crowd. I have included pics of the Pizza Rolls, but it's up to you how you want to incorporate them in the design.Poster should include our logo, the pizza rolls, and can include a drink to illustrate the combo as well. ( we offer710 ml zint bottle products and vorn bottled waters)Main Text: Try our amazing new Pizza Rolls! Message to get accross: $6.00 for a Pizza Roll and drink.Small Print: Avail after 11am, while supplies last. Includes one pizza roll and one bottled drink of choice. Taxes extra.

Target Market(s)

Broad, but mainly high school aged kids

Industry/Entity Type

Bakery

Colors

Designer to choose colors to be used in the design.

Requirements
Must have
• Text: " Try our amazing new PIzza Rolls!:
• $6 Pizza Roll Combo (Pizza Roll and a drink)
Nice to have
• Pic of the PIzza Roll (photo shopped if needed to improve esthetics)
• Pic of a Bottled 710ml zint drink
Should not have
• Any animal product references, as we are a Vegan shop.

```html
<!DOCTYPE html>
<html lang="en">
<head>
<meta charset="utf-8">
<title>Pizza Roll Combo Poster</title>
<link rel="stylesheet" href="https://fonts.googleapis.com/css2?family=Alfa+Slab+One&family=Montserrat:wght@800;900&family=Oswald:wght@300&family=Pacifico&family=Roboto:wght@300&display=swap">
<style>
  :root {
    --purple-deep: #4a10b8;
    --purple-bright: #7a18f0;
    --purple-badge: #6a3f96;
    --orange: #f4610f;
    --amber: #fcb72a;
    --yellow: #ffd21f;
    --yellow-light: #fff06a;
    --gold-edge: #8a5a00;
    --brown: #3b2410;
    --red: #e2401f;
    --white: #ffffff;
  }
  * { margin: 0; padding: 0; box-sizing: border-box; }
  html, body { width: 849px; height: 1200px; overflow: hidden; }
  body { background: var(--brown); }
  .poster {
    position: relative;
    width: 849px;
    height: 1200px;
    overflow: hidden;
    background:
      radial-gradient(ellipse 520px 420px at 330px 420px, var(--yellow) 0%, rgba(252,183,42,0.8) 35%, rgba(244,97,15,0) 75%),
      radial-gradient(ellipse 500px 300px at 560px 830px, var(--amber) 0%, rgba(244,97,15,0) 80%),
      linear-gradient(180deg, var(--purple-deep) 0%, var(--purple-bright) 30%, var(--orange) 52%, var(--orange) 78%, var(--brown) 100%);
  }
  .swoosh { position: absolute; inset: 0; }
  .combo-photo { position: absolute; left: 0; top: 0; width: 849px; height: 520px; }
  .combo-band { position: absolute; left: 0; top: 0; width: 849px; height: 700px; }
  .combo-title {
    position: absolute;
    left: 18px; top: 468px;
    transform: rotate(-6deg);
    transform-origin: left top;
    line-height: 1;
  }
  .combo-title .line-one {
    display: block;
    font-family: "Alfa Slab One", serif;
    font-size: 50px;
    color: var(--red);
    letter-spacing: 1px;
  }
  .combo-title .line-two {
    display: block;
    margin: -2px 0 0 32px;
    font-family: "Montserrat", sans-serif;
    font-weight: 900;
    font-size: 70px;
    color: var(--purple-badge);
  }
  .price {
    position: absolute;
    left: 396px; top: 400px;
    font-family: "Montserrat", sans-serif;
    font-weight: 900;
    color: var(--yellow);
    text-shadow:
      -2px 0 0 var(--gold-edge), 2px 0 0 var(--gold-edge),
      0 -2px 0 var(--gold-edge), 0 2px 0 var(--gold-edge),
      4px 5px 6px rgba(0,0,0,0.45);
    line-height: 1;
  }
  .price .currency { font-size: 80px; vertical-align: 90px; margin-right: 2px; }
  .price .amount { font-size: 250px; }
  .try-out {
    position: absolute;
    left: 214px; top: 664px;
    font-family: "Oswald", sans-serif;
    font-weight: 300;
    font-size: 52px;
    color: var(--purple-badge);
    line-height: 1;
  }
  .amazing {
    position: absolute;
    left: 282px; top: 676px;
    font-family: "Pacifico", cursive;
    font-size: 86px;
    color: var(--purple-badge);
    line-height: 1.2;
    white-space: nowrap;
    transform: scale(1.05, 0.78);
    transform-origin: left top;
  }
  .new-badge { position: absolute; left: 30px; top: 716px; width: 146px; height: 136px; }
  .new-badge span {
    position: absolute;
    left: 14px; top: 42px;
    transform: rotate(-12deg);
    font-family: "Montserrat", sans-serif;
    font-weight: 900;
    font-size: 44px;
    color: var(--white);
  }
  .headline {
    position: absolute;
    font-family: "Alfa Slab One", serif;
    color: var(--yellow);
    background: repeating-linear-gradient(45deg, var(--yellow) 0 2px, var(--yellow-light) 2px 4px);
    -webkit-background-clip: text;
    background-clip: text;
    -webkit-text-fill-color: transparent;
    filter: drop-shadow(2px 3px 0 #9a5a10) drop-shadow(0 4px 6px rgba(0,0,0,0.35));
    line-height: 1;
    letter-spacing: 2px;
    white-space: nowrap;
    transform-origin: left top;
  }
  .headline.pizza { left: 118px; top: 774px; font-size: 178px; transform: scale(0.85, 1.08); }
  .headline.rolls { left: 304px; top: 952px; font-size: 170px; transform: scale(0.84, 1.02); }
  .fine-print {
    position: absolute;
    left: 0; right: 0; top: 1126px;
    text-align: center;
    font-family: "Roboto", sans-serif;
    font-weight: 300;
    font-size: 19px;
    line-height: 28px;
    color: var(--white);
  }
</style>
</head>
<body>
<main class="poster">
  <svg class="swoosh" viewBox="0 0 849 1200" aria-hidden="true">
    <path d="M120 0 C 60 200, 180 420, 500 470 C 700 500, 849 460, 849 460 L849 560 C 700 560, 400 560, 200 420 C 60 300, 40 120, 60 0 Z" fill="#ffb020" opacity="0.35"/>
  </svg>

  <svg class="combo-photo" viewBox="0 0 849 520" role="img" aria-label="Photo of a chilled bottle of Zint cola beside three baked pizza rolls on a red gingham napkin">
    <defs>
      <linearGradient id="napkinTone" x1="0" y1="0" x2="1" y2="1">
        <stop offset="0" stop-color="#e8c9a8"/>
        <stop offset="0.5" stop-color="#d98a4a"/>
        <stop offset="1" stop-color="#d84a4a"/>
      </linearGradient>
      <linearGradient id="bottleTone" x1="0" y1="0" x2="0" y2="1">
        <stop offset="0" stop-color="#d8dede"/>
        <stop offset="0.3" stop-color="#5a1e14"/>
        <stop offset="1" stop-color="#2a0d08"/>
      </linearGradient>
    </defs>
    <polygon points="290,40 560,20 849,210 849,310 700,480 420,470 210,260" fill="url(#napkinTone)"/>
    <polygon points="175,120 235,95 450,420 390,450" fill="url(#bottleTone)"/>
  </svg>

  <svg class="combo-band" viewBox="0 0 849 700" aria-hidden="true">
    <path d="M0 458 C 150 430, 330 425, 470 440 L 520 650 C 380 615, 180 610, 0 668 Z" fill="var(--white)"/>
    <path d="M0 458 C 150 430, 330 425, 470 440" fill="none" stroke="#1d3a8a" stroke-width="2"/>
    <path d="M0 668 C 180 610, 380 615, 520 650" fill="none" stroke="#1d3a8a" stroke-width="2"/>
    <path d="M400 395 C 480 350, 600 360, 640 400 C 680 450, 670 560, 620 640 C 590 690, 520 695, 470 650 C 420 600, 380 520, 380 450 C 380 420, 385 405, 400 395 Z" fill="var(--purple-badge)" stroke="var(--white)" stroke-width="3"/>
  </svg>

  <h2 class="combo-title"><span class="line-one">PIZZA ROLL</span><span class="line-two">COMBO</span></h2>
  <div class="price"><span class="currency">$</span><span class="amount">6</span></div>

  <p class="try-out">TRY OUT</p>
  <p class="amazing">our amazing</p>

  <div class="new-badge">
    <svg viewBox="0 0 146 136" width="146" height="136" aria-hidden="true">
      <path d="M20 20 C 60 0, 130 10, 142 30 C 150 50, 110 110, 80 128 C 55 140, 20 120, 8 80 C 0 50, 5 28, 20 20 Z" fill="var(--purple-badge)"/>
    </svg>
    <span>NEW</span>
  </div>

  <h1>
    <span class="headline pizza">PIZZA</span>
    <span class="headline rolls">ROLLS</span>
  </h1>

  <p class="fine-print">Available after 11am, while supplies last.<br>Includes one pizza roll and one bottled drink of choice. Taxes extra.</p>
</main>
</body>
</html>
```